Menu Edit

Hello. We need a pricing edit on our current menu and new logo swapped (we already have the new logo), as well as colour changes. Also, we require a takeaway menu, in-store menu and footpath a-frame edit as well. I have attached the files bellow.

```html
<!DOCTYPE html>
<html lang="en">
<head>
<meta charset="utf-8">
<title>Tide &amp; Tackle – A-frames and Menu</title>
<link rel="stylesheet" href="https://fonts.googleapis.com/css2?family=Merriweather:wght@300;400;700;900&family=Barlow+Semi+Condensed:wght@500;600&family=Montserrat:wght@700&display=swap">
<style>
:root{
  --page:#ffffff;
  --panel:#231f20;
  --blue:#0a97f2;
  --white:#ffffff;
  --soft:#d9d9d9;
  --rule:#8a8a8a;
  --badge-green:#1fb25a;
  --badge-yellow:#f4d71f;
  --badge-teal:#22c1c3;
  --badge-orange:#ff6b1a;
  --badge-red:#ef3b24;
}
*{box-sizing:border-box;margin:0;padding:0}
html,body{width:1200px;height:2715px;overflow:hidden;background:var(--page)}
body{font-family:"Merriweather",Georgia,serif;font-weight:300;color:var(--white)}
.canvas{position:relative;width:1200px;height:2715px}
.panel{position:absolute;background:var(--panel);overflow:hidden}
.abs{position:absolute}
.center{left:0;right:0;text-align:center}

/* brand lockup */
.brand{position:absolute;display:flex;align-items:center}
.brand-dot{border-radius:50%;background:var(--blue);flex:none}
.brand-text{display:flex;flex-direction:column;align-items:center}
.brand-name{font-weight:300;letter-spacing:.5px;white-space:nowrap;line-height:1}
.brand-tag{font-family:"Barlow Semi Condensed",sans-serif;font-weight:600;color:var(--blue);line-height:1;white-space:nowrap}

.blue{color:var(--blue)}
.btn{position:absolute;background:var(--blue);color:var(--white);border-radius:4px;font-weight:700;display:flex;align-items:center;justify-content:center;letter-spacing:.3px}
.phone{font-family:"Montserrat",sans-serif;font-weight:700;display:flex;align-items:center;justify-content:center;gap:10px}
.rule{position:absolute;height:3px;background:var(--blue)}

.badges{position:absolute;display:grid;gap:4px}
.badge{border-radius:1px}
.b-green{background:var(--badge-green)}
.b-yellow{background:var(--badge-yellow)}
.b-teal{background:var(--badge-teal)}
.b-orange{background:var(--badge-orange);border-radius:3px}
.b-red{background:var(--badge-red);border-radius:3px}

/* menu pages */
.sec-title{position:absolute;font-family:"Barlow Semi Condensed",sans-serif;font-weight:600;font-size:20px;letter-spacing:.3px;line-height:1}
.sec-title::after{content:"";position:absolute;left:0;top:27px;width:16px;height:2px;background:var(--blue)}
.sec-title .plus{color:var(--blue)}
.list{position:absolute;list-style:none;font-size:9.5px;color:var(--soft)}
.list li{height:19px;line-height:17px;border-bottom:1px solid var(--rule)}
.list.tight li{height:17px;line-height:15px}
.item-name{color:var(--blue)}
.frame{position:absolute;border:1px solid var(--soft);padding:3px}
.frame::before{content:"";position:absolute;inset:3px;border:1px solid var(--soft)}
.dish{position:absolute;font-size:9.5px;color:var(--soft)}
.dish .head{border-bottom:1px solid var(--rule);padding-bottom:3px;margin-bottom:4px}
.dish p{font-size:8.6px;line-height:1.25}
.note{position:absolute;font-size:8.6px;color:var(--soft)}
</style>
</head>
<body>
<div class="canvas">

  <!-- A-frame: opening hours -->
  <section class="panel aframe-hours" style="left:89px;top:69px;width:484px;height:717px">
    <div class="brand" style="left:40px;top:48px;gap:22px">
      <span class="brand-dot" style="width:22px;height:22px"></span>
      <div class="brand-text" style="gap:6px">
        <span class="brand-name" style="font-size:31px">TIDE &amp; TACKLE</span>
        <span class="brand-tag" style="font-size:18px">FISH AND CHIPS</span>
      </div>
    </div>
    <div class="abs center blue" style="top:191px;font-size:12px;letter-spacing:6px;font-weight:400">WELCOME</div>
    <div class="abs center" style="top:238px;font-size:36px;font-weight:900">Open Every Day</div>
    <div class="abs center" style="top:297px;font-size:22px;line-height:27px">
      <div><span class="blue">Tues – Sun</span>&nbsp; Lunch 12pm – 3pm</div>
      <div><span class="blue">Tues – Sun</span>&nbsp; Dinner 5pm – 9pm</div>
    </div>
    <div class="abs center" style="top:366px;font-size:19px;line-height:25px">
      <div>DINE IN <span class="blue">|</span> TAKEAWAY</div>
      <div>ONLINE ORDERING &amp; DELIVER</div>
      <div>FRESH RETAIL</div>
    </div>
    <div class="abs center" style="top:456px;font-size:14px">BYO Welcome! Wine, Beer &amp; Spirits / Soft Drinks Available</div>
    <div class="rule" style="left:38px;width:408px;top:480px"></div>
    <div class="abs center" style="top:490px;font-size:15px;line-height:22px">
      <div>Choose your preparation:</div>
      <div>PANKO CRUMBED / TEMPURA BATTERED / GRILLED</div>
    </div>
    <div class="rule" style="left:38px;width:408px;top:537px"></div>
    <div class="abs center phone" style="top:567px;font-size:48px">
      <svg width="46" height="38" viewBox="0 0 46 38" aria-hidden="true"><path fill="#fff" d="M4 12c0-6 8-9 19-9s19 3 19 9l-1 4h-8l-1-4c-3-1-6-1-9-1s-6 0-9 1l-1 4H5zM11 18h24l5 17H6z"/><g fill="#231f20"><rect x="16" y="22" width="3" height="3"/><rect x="22" y="22" width="3" height="3"/><rect x="28" y="22" width="3" height="3"/><rect x="16" y="28" width="3" height="3"/><rect x="22" y="28" width="3" height="3"/><rect x="28" y="28" width="3" height="3"/></g></svg>
      3555 0142
    </div>
    <div class="btn" style="left:69px;top:643px;width:348px;height:34px;border-radius:8px;font-family:'Montserrat',sans-serif;font-size:20px">www.tideandtackle.com.au</div>
  </section>

  <!-- A-frame: we're open -->
  <section class="panel aframe-open" style="left:617px;top:69px;width:484px;height:717px">
    <div class="brand" style="left:40px;top:48px;gap:22px">
      <span class="brand-dot" style="width:22px;height:22px"></span>
      <div class="brand-text" style="gap:6px">
        <span class="brand-name" style="font-size:31px">TIDE &amp; TACKLE</span>
        <span class="brand-tag" style="font-size:18px">FISH AND CHIPS</span>
      </div>
    </div>
    <div class="abs center" style="top:150px;font-size:86px;line-height:84px;font-weight:300;letter-spacing:2px">WE’RE<br>OPEN!</div>
    <div class="btn" style="left:136px;top:368px;width:213px;height:35px;font-size:16px">ORDER FOR PICKUP</div>
    <div class="abs center" style="top:431px;font-size:19px;display:flex;justify-content:center;align-items:center;gap:8px">
      <svg width="16" height="16" viewBox="0 0 16 16" aria-hidden="true"><circle cx="8" cy="8" r="7" fill="none" stroke="#1fb25a" stroke-width="1.6"/><path d="M1 8h14M8 1c3 3 3 11 0 14M8 1c-3 3-3 11 0 14" fill="none" stroke="#1fb25a" stroke-width="1.2"/></svg>
      www.tideandtackle.com.au
    </div>
    <div class="abs center phone" style="top:457px;font-size:44px">
      <svg width="42" height="35" viewBox="0 0 46 38" aria-hidden="true"><path fill="#fff" d="M4 12c0-6 8-9 19-9s19 3 19 9l-1 4h-8l-1-4c-3-1-6-1-9-1s-6 0-9 1l-1 4H5zM11 18h24l5 17H6z"/></svg>
      3555 0142
    </div>
    <div class="btn" style="left:136px;top:548px;width:213px;height:35px;font-size:16px">ORDER FOR DELIVERY</div>
    <div class="badges" style="left:136px;top:603px;grid-template-columns:35px 82px 89px;grid-auto-rows:35px">
      <span class="badge b-green"></span><span class="badge b-yellow"></span><span class="badge b-teal"></span>
    </div>
    <div class="badges" style="left:136px;top:645px;grid-template-columns:92px 110px;grid-auto-rows:20px;column-gap:12px">
      <span class="badge b-orange"></span><span class="badge b-red"></span>
    </div>
  </section>

  <!-- Menu cover -->
  <section class="panel menu-cover" style="left:218px;top:838px;width:755px;height:570px">
    <div class="brand" style="left:130px;top:62px;gap:48px">
      <span class="brand-dot" style="width:30px;height:30px"></span>
      <div class="brand-text" style="gap:8px">
        <span class="brand-name" style="font-size:42px">TIDE &amp; TACKLE</span>
        <span class="brand-tag" style="font-size:25px">FISH AND CHIPS</span>
      </div>
    </div>
    <div class="abs" style="left:88px;width:580px;top:183px;text-align:center;font-size:12.4px;line-height:15px">
      Our premium quality fish is wild caught and sustainably farmed from pristine Australian &amp; New Zealand waters, delivered in-store every day for you to enjoy! &nbsp;Our seafood is deep-fried to golden goodness with premium 100% Australian grown and pressed sunflower oil.
      <div style="margin-top:6px">(All seafood is subject to daily fresh market availability).</div>
    </div>
    <div class="abs" style="left:120px;width:240px;top:289px;text-align:center;font-size:11.5px;line-height:18px">Gluten friendly options are available.<br>Our takeaway packaging is <span style="display:inline-block;width:10px;height:10px;border:1px solid #fff;border-radius:50%;vertical-align:-1px"></span> friendly.</div>
    <div class="abs" style="left:390px;width:220px;top:289px;text-align:center;font-size:11.5px;line-height:18px">Menu substitutions are not available.<br>Public holiday surcharge 15%.</div>
    <div class="btn" style="left:183px;top:377px;width:167px;height:27px;font-size:12.5px">ORDER FOR PICKUP</div>
    <div class="btn" style="left:396px;top:377px;width:167px;height:27px;font-size:12.5px">ORDER FOR DELIVERY</div>
    <div class="abs" style="left:165px;width:200px;top:420px;text-align:center;font-size:11px">● www.tideandtackle.com.au</div>
    <div class="abs phone" style="left:165px;width:200px;top:437px;font-size:16px;gap:5px">☎ 3555 0142</div>
    <div class="badges" style="left:396px;top:416px;grid-template-columns:29px 64px 70px;grid-auto-rows:27px;gap:3px">
      <span class="badge b-green"></span><span class="badge b-yellow"></span><span class="badge b-teal"></span>
    </div>
    <div class="badges" style="left:396px;top:449px;grid-template-columns:72px 84px;grid-auto-rows:15px;column-gap:11px">
      <span class="badge b-orange"></span><span class="badge b-red"></span>
    </div>
    <div class="abs" style="left:182px;top:490px;font-size:20px;display:flex;align-items:center;gap:12px">
      Follow us <span style="width:20px;height:20px;border-radius:4px;background:#e4406f"></span> tideandtackle_riverside
    </div>
  </section>

  <!-- Menu page 1 -->
  <section class="panel menu-page" style="left:218px;top:1443px;width:755px;height:570px">
    <h2 class="sec-title" style="left:50px;top:42px">STARTERS <span class="plus">+</span> SIDES</h2>
    <ul class="list" style="left:49px;top:76px;width:302px">
      <li>Crumbed Calamari (8)</li><li>Salt &amp; Pepper Calamari (8)</li><li>Crumbed Sea Scallop</li><li>Crumbed Prawn</li><li>BBQ Prawn Skewer</li><li>Onion Rings (8)</li><li>Popcorn Chicken</li><li>Potato Scallop</li><li>Grilled Halloumi (3 slices)</li><li>Fried Halloumi (3 slices, crumbed)</li>
    </ul>
    <h2 class="sec-title" style="left:50px;top:300px">CHIPS</h2>
    <ul class="list" style="left:50px;top:330px;width:302px">
      <li>Chips GF</li><li>Beer Battered Chips</li><li>Sweet Potato Chips</li>
    </ul>
    <h2 class="sec-title" style="left:50px;top:426px">SAUCES</h2>
    <ul class="list" style="left:50px;top:456px;width:308px">
      <li>Tartare, Aioli, Tomato &amp; Chipotle Mayonnaise</li>
    </ul>

    <div class="frame" style="left:390px;top:24px;width:313px;height:276px"></div>
    <h2 class="sec-title" style="left:402px;top:42px">BURGERS <span class="plus">+</span> TACOS</h2>
    <div class="dish" style="left:402px;top:78px;width:288px"><div class="head"><span class="item-name">Fish Burger</span> &amp; chips</div><p>Crumbed cod fillet, shredded lettuce, tomato &amp; tartare sauce in a toasted bun.</p></div>
    <div class="dish" style="left:402px;top:134px;width:288px"><div class="head"><span class="item-name">Fish Tacos</span> (3) &amp; chips</div><p>Beer battered cod, shredded red &amp; green cabbage, carrot, chipotle mayonnaise in soft flour tortillas.</p></div>
    <div class="dish" style="left:402px;top:190px;width:288px"><div class="head"><span class="item-name">Chicken Burger</span> &amp; chips</div><p>Grilled free range chicken tenders, shredded lettuce, tomato, cheese, avocado, aioli in a toasted bun.</p></div>
    <div class="dish" style="left:402px;top:246px;width:288px"><div class="head"><span class="item-name">Steak Burger</span> &amp; chips</div><p>Grilled grass fed rib fillet, shredded lettuce, tomato, cheese, caramelised onion, BBQ sauce in a toasted bun.</p></div>

    <h2 class="sec-title" style="left:390px;top:386px">CHILDREN’S FISH <span class="plus">+</span> CHIPS</h2>
    <ul class="list" style="left:390px;top:414px;width:306px">
      <li><span class="item-name">Fish Fingers</span> (4) &amp; chips</li><li><span class="item-name">Crumbed Calamari</span> (4) &amp; chips</li><li><span class="item-name">Popcorn Chicken</span> &amp; chips</li>
    </ul>
  </section>

  <!-- Menu page 2 -->
  <section class="panel menu-page" style="left:218px;top:2063px;width:755px;height:570px">
    <div class="frame" style="left:49px;top:22px;width:314px;height:272px"></div>
    <h2 class="sec-title" style="left:62px;top:40px">FISH <span class="plus">+</span> CHIPS</h2>
    <div class="note" style="left:62px;top:70px">Served with your choice of chips, tartare sauce &amp; lemon.</div>
    <ul class="list tight" style="left:62px;top:88px;width:288px">
      <li><span class="item-name">Cod</span> &amp; chips (NZ, wild caught)</li>
      <li><span class="item-name">Whiting</span> &amp; chips (QLD, wild caught, crumbed only)</li>
      <li><span class="item-name">Flathead</span> &amp; chips (SA, wild caught, beer battered only)</li>
      <li><span class="item-name">Snapper</span> &amp; chips (NT, wild caught)</li>
      <li><span class="item-name">Barramundi</span> &amp; chips (NT, ocean farmed)</li>
      <li><span class="item-name">Salmon</span> &amp; chips (TAS, ocean farmed)</li>
      <li><span class="item-name">Crumbed Calamari</span> (8) &amp; chips</li>
      <li><span class="item-name">Salt &amp; Pepper Calamari</span> (8) &amp; chips</li>
      <li><span class="item-name">Crumbed Prawns</span> (5) &amp; chips</li>
      <li><span class="item-name">BBQ Prawn Skewers</span> (5) &amp; chips</li>
    </ul>
    <div class="note" style="left:62px;width:288px;top:266px;text-align:center;line-height:12px"><span class="item-name">Made fresh to order</span> | Choose your preparation:<br>GRILLED / CRUMBED / BEER BATTERED</div>

    <h2 class="sec-title" style="left:390px;top:40px">SALADS</h2>
    <div class="note" style="left:390px;top:75px">Freshly prepared to order using local produce.</div>
    <div class="dish" style="left:390px;top:110px;width:308px"><div class="head item-name">Greek</div><p>Lettuce, cucumber, tomato, red onion, Kalamata olives, feta, Greek peppers, wild oregano, dressed in Greek extra virgin olive oil vinaigrette.</p></div>
    <div class="dish" style="left:390px;top:165px;width:308px"><div class="head item-name">Roast Pumpkin</div><p>Roast pumpkin, wild rocket, Parmigiano Reggiano, toasted pine nuts, dressed in Greek extra virgin olive oil &amp; vintage balsamic vinegar.</p></div>
    <div class="dish" style="left:390px;top:220px;width:308px"><div class="head item-name">Slaw</div><p>Shredded red &amp; green cabbage, carrot, tossed in a light mayonnaise dressing.</p></div>
    <div class="dish" style="left:390px;top:266px;width:308px"><div class="head item-name">Asian Slaw</div><p>Shredded red &amp; green cabbage, carrot, spring onion, crispy noodles, sesame seeds, tossed in a sweet soy dressing.</p></div>

    <h2 class="sec-title" style="left:49px;top:359px">COOKED SEAFOOD PLATTERS</h2>
    <div class="note" style="left:49px;top:393px;width:610px;line-height:11px">Cooked Seafood Platters include: whiting, calamari, salt &amp; pepper calamari, prawns, sea scallops, chips, one of our freshly made salads, tartare sauce &amp; lemon.</div>
    <ul class="list" style="left:49px;top:426px;width:655px;font-weight:700">
      <li>Cooked Platter for One</li><li>Cooked Platter for Two</li><li>Cooked Platter for Three</li>
    </ul>
    <div class="note" style="left:0;right:0;top:504px;text-align:center">Our seafood platters are available crumbed only.</div>
  </section>

</div>
</body>
</html>
```